Breakfast Cafe - The Sunny Nook

It is for my breakfast and lunch cafe with a hawaiian / beach theme. I am open 7 days a week from 7am to 2pm. We serve traditional American food such as omelettes, pancakes, burgers and sandwiches. I'll upload my old card and my new logo to be used. We have a lot of day to day regulars who eat there during the week, our t-shirts actually say 'Locals Only' on them. Hope this helps. Thanks.

Target Market(s)

anyone who has an appetite!

Industry/Entity Type

American Restaurant

Contact Information for Business Card

4815C Marlow Grove Avenue
Long Beach, California
(555) 731-2294

Requirements
Must have
• Address and phone number easily readable.
Nice to have
• beach or tropical theme

```html
<!DOCTYPE html>
<html lang="en">
<head>
<meta charset="utf-8">
<title>The Sunny Nook – Business Card</title>
<link rel="stylesheet" href="https://fonts.googleapis.com/css2?family=Bebas+Neue&family=Parisienne&display=swap">
<style>
  :root {
    --page-bg: #ebe7e2;
    --frost: #dcd8d3;
    --wood-light: #a35a2e;
    --wood-mid: #7c3f1e;
    --wood-dark: #4f2412;
    --ring: #6a3418;
    --cream: #f4e8da;
    --blush: #e9c9c0;
    --brand-green: #3f9a6b;
    --sun: #f2a33a;
    --sky: #cfe3e6;
    --sand: #e8d6b8;
  }
  * { margin: 0; padding: 0; box-sizing: border-box; }
  html, body {
    width: 1200px;
    height: 969px;
    overflow: hidden;
    background: var(--page-bg);
  }
  .card {
    position: absolute;
    left: 100px;
    top: 199px;
    width: 1000px;
    height: 571px;
    border-radius: 24px;
    overflow: hidden;
    background: linear-gradient(160deg, #e6e3df 0%, var(--frost) 60%, #cfcac4 100%);
    box-shadow: 0 10px 30px rgba(60, 40, 25, 0.18);
  }
  .wood-panel {
    position: absolute;
    left: 0;
    top: 0;
    width: 770px;
    height: 100%;
    background:
      linear-gradient(90deg, rgba(0,0,0,0.08) 0%, rgba(255,255,255,0.05) 35%, rgba(0,0,0,0.12) 100%),
      linear-gradient(180deg, var(--wood-light) 0%, var(--wood-mid) 55%, var(--wood-dark) 100%);
  }
  .scene-disc {
    position: absolute;
    left: 488px;
    top: 26px;
    width: 518px;
    height: 518px;
    border-radius: 50%;
    border: 16px solid var(--ring);
    background:
      radial-gradient(circle at 50% 95%, var(--sand) 0%, rgba(232,214,184,0) 45%),
      linear-gradient(180deg, var(--sky) 0%, #e4e9e6 55%, var(--sand) 100%);
  }
  .brand {
    position: absolute;
    left: 555px;
    top: 90px;
    width: 400px;
    text-align: center;
  }
  .brand-dot {
    display: block;
    width: 240px;
    height: 240px;
    margin: 0 auto;
    border-radius: 50%;
    background: var(--sun);
  }
  .brand-name {
    display: block;
    margin-top: 36px;
    font-family: "Bebas Neue", sans-serif;
    font-size: 62px;
    line-height: 1;
    letter-spacing: 1px;
    color: var(--brand-green);
  }
  .contact {
    position: absolute;
    left: 57px;
    top: 66px;
    font-family: "Bebas Neue", sans-serif;
    color: var(--cream);
  }
  .contact .address {
    font-size: 33px;
    line-height: 1.05;
    letter-spacing: 0.5px;
  }
  .contact .phone {
    font-size: 41px;
    line-height: 1.1;
    letter-spacing: 0.5px;
  }
  .about {
    position: absolute;
    left: 57px;
    top: 260px;
    font-family: "Bebas Neue", sans-serif;
    color: var(--cream);
  }
  .about .kind {
    font-size: 31px;
    line-height: 1.1;
    letter-spacing: 0.5px;
  }
  .about .hours {
    font-size: 24px;
    line-height: 1.35;
    letter-spacing: 0.4px;
  }
  .about .menu {
    font-size: 20px;
    line-height: 1.5;
    letter-spacing: 0.4px;
  }
  .tagline {
    position: absolute;
    left: 57px;
    top: 432px;
    font-family: "Parisienne", cursive;
    font-size: 64px;
    color: var(--blush);
  }
</style>
</head>
<body>
  <div class="card">
    <div class="wood-panel"></div>
    <div class="scene-disc" role="img" aria-label="Soft beach scene with palms, ocean, ship and gulls"></div>

    <div class="brand">
      <span class="brand-dot"></span>
      <span class="brand-name">The Sunny Nook</span>
    </div>

    <div class="contact">
      <p class="address">4815C Marlow Grove Avenue<br>Long Beach, California</p>
      <p class="phone">P.(555) 731-2294</p>
    </div>

    <div class="about">
      <p class="kind">Breakfast &amp; Lunch Cafe</p>
      <p class="hours">Open 7 days a week from 7am to 2pm.</p>
      <p class="menu">Serving traditional American food</p>
    </div>

    <p class="tagline">Locals Only</p>
  </div>
</body>
</html>
```